Business Card Design Project

Looking for a logo and business card for a Real State Business i will be opening. The name is not choosen yet , but will probably be RWT IMOVEIS.
I was thinking black and silver colors, but am open to nice ideas.
I did add a business card that i liked a lot, am looking for something like that, with logo in black or silver in a black card. The logo i was thinking in the letters RWT as i uploaded or something or little and cute buildings or a house...just ideas, can be any nice logo.
Updates

You guys can add other colors if you want, I like colors very "BRIGHT" and "open", like red, pink, strong colors. almost glow in the dark colors. lol

Designers,

I've increased more 88 dollars in the budget for 1st place cause I will want envelope designs... small and big sizes.

So 1st place is now U$248,00. 

No need to send the envelope designs right now... only the business cards designs.

Thank you.

Industry/Entity Type

Business

Requirements
Must have
• Marcela Tavares Rocha

www.RWTimoveis-exemplo.com.br

+554187316042

marcela@rwtimoveis-exemplo.com.br

```html
<!DOCTYPE html>
<html lang="pt-BR">
<head>
<meta charset="utf-8">
<title>RWT Imoveis – Cartão de visita</title>
<link rel="stylesheet" href="https://fonts.googleapis.com/css2?family=Michroma&display=swap">
<style>
  :root {
    --page-bg: #e9e6e1;
    --card-light: #e4e4e4;
    --card-light-edge: #cfcfcf;
    --card-dark: #050505;
    --accent-green: #8cc63f;
    --accent-green-deep: #6aa02a;
    --ink-dark: #111111;
    --ink-light: #f2f2f2;
  }
  * { box-sizing: border-box; margin: 0; padding: 0; }
  html, body {
    width: 1200px;
    height: 1024px;
    overflow: hidden;
    background: var(--page-bg);
  }
  .canvas {
    position: relative;
    width: 1200px;
    height: 1024px;
    display: flex;
    flex-direction: column;
    align-items: center;
    justify-content: center;
    gap: 40px;
  }
  .card {
    position: relative;
    width: 800px;
    height: 456px;
    overflow: hidden;
    box-shadow: 0 10px 30px rgba(0,0,0,0.18);
  }
  .card--front {
    background: linear-gradient(135deg, #f1f1f1 0%, var(--card-light) 55%, var(--card-light-edge) 100%);
  }
  .card--back {
    background: var(--card-dark);
  }
  .grid-texture {
    position: absolute;
    inset: 0;
    background: linear-gradient(180deg, rgba(255,255,255,0.35), rgba(200,200,200,0.25));
  }
  .accent-band {
    position: absolute;
    top: 0;
    right: 0;
    width: 52px;
    height: 100%;
    background: linear-gradient(90deg, var(--accent-green-deep), var(--accent-green));
  }
  .card--back .accent-band {
    left: 0;
    right: auto;
    background: linear-gradient(270deg, var(--accent-green-deep), var(--accent-green));
  }
  .contact {
    position: absolute;
    right: 96px;
    top: 150px;
    list-style: none;
    text-align: right;
    font-family: "Michroma", sans-serif;
    font-variant: small-caps;
  }
  .contact li {
    display: flex;
    justify-content: flex-end;
    align-items: center;
    gap: 14px;
    color: var(--ink-dark);
    font-size: 17px;
    letter-spacing: 0.5px;
    line-height: 1;
    margin-bottom: 22px;
  }
  .contact .contact__name {
    color: var(--accent-green);
    font-size: 27px;
    margin-bottom: 26px;
  }
  .contact .contact__phone { font-size: 21px; }
  .marker {
    display: inline-block;
    width: 14px;
    height: 11px;
    background: var(--accent-green);
    flex: none;
  }
  .brand {
    position: absolute;
    right: 80px;
    top: 50%;
    transform: translateY(-50%);
    display: flex;
    align-items: center;
    gap: 18px;
    font-family: "Michroma", sans-serif;
    font-size: 44px;
    letter-spacing: 2px;
    color: var(--ink-light);
  }
  .brand .marker {
    width: 22px;
    height: 22px;
  }
</style>
</head>
<body>
  <main class="canvas">
    <section class="card card--front" aria-label="Frente do cartão">
      <div class="grid-texture" role="img" aria-label="Textura de quadrados cinza claros"></div>
      <div class="accent-band" role="img" aria-label="Faixa de quadrados verdes"></div>
      <ul class="contact">
        <li class="contact__name">Marcela Tavares Rocha <span class="marker"></span></li>
        <li class="contact__phone">+554187316042 <span class="marker"></span></li>
        <li class="contact__email">marcela@rwtimoveis-exemplo.com.br <span class="marker"></span></li>
        <li class="contact__web">www.RWTimoveis-exemplo.com.br <span class="marker"></span></li>
      </ul>
    </section>

    <section class="card card--back" aria-label="Verso do cartão">
      <div class="accent-band" role="img" aria-label="Faixa de quadrados verdes sobre fundo preto"></div>
      <div class="brand"><span class="marker"></span>RWT IMOVEIS</div>
    </section>
  </main>
</body>
</html>
```